One of a Kind Clean Business Card

We need to design a new business card template for our company. Our company designs and produced merchandising displays. You can see a sample of what we produce on our site www.qorvanexhibits.net. I have uploaded our logo in vector format, as well as a picture of our current business cards. We want a totally different look. We want simple and clean, looking forward to seeing what people create.
Updates

I would like to update the address for Qorvan Display Group Inc. 518 E Tollmere Ln Arlington Heights, IL 60017 Would also note. No QR codes

Industry/Entity Type

Business

Contact Information for Business Card

Need a 1 sided business card designed.

Font styles to use
Serif

Requirements
Must have
• Easy to view; Clean Design
Nice to have
• Features that promote engineering and creativity
Should not have
• Too much clutter, keep it simple

```html
<!DOCTYPE html>
<html lang="en">
<head>
<meta charset="utf-8">
<title>Qorvan Display Group Inc. — Business Card</title>
<link rel="stylesheet" href="https://fonts.googleapis.com/css2?family=Open+Sans:wght@400;600&display=swap">
<style>
  :root {
    --stage: #8e8e8e;
    --stage-light: #979797;
    --card-white: #ffffff;
    --brand-red: #88000a;
    --accent-red: #951119;
    --ink: #111111;
    --text-grey: #3a3a3a;
  }
  html, body {
    margin: 0;
    padding: 0;
    width: 1200px;
    height: 900px;
    overflow: hidden;
  }
  body {
    position: relative;
    background: linear-gradient(to bottom, var(--stage), var(--stage-light));
    font-family: "Open Sans", Arial, sans-serif;
  }
  .card {
    position: absolute;
    top: 306px;
    width: 440px;
    height: 271px;
    overflow: hidden;
  }
  .card--front { left: 149px; background: var(--card-white); }
  .card--back { left: 608px; background: var(--brand-red); }

  .name-tab { position: absolute; left: 0; top: 25px; }
  .holder-name {
    position: absolute;
    left: 36px;
    top: 35px;
    margin: 0;
    font-size: 17px;
    font-weight: 400;
    color: var(--brand-red);
    letter-spacing: 0.2px;
  }
  .company-name {
    position: absolute;
    margin: 0;
    font-weight: 400;
    white-space: nowrap;
  }
  .card--front .company-name {
    left: 246px;
    top: 104px;
    font-size: 15px;
    color: var(--brand-red);
  }
  .card--back .company-name {
    left: 0;
    right: 0;
    top: 146px;
    text-align: center;
    font-size: 20px;
    color: var(--card-white);
  }
  .contact-list {
    position: absolute;
    left: 31px;
    top: 172px;
    margin: 0;
    padding: 0;
    list-style: none;
    font-size: 12px;
    line-height: 16px;
    color: var(--text-grey);
  }
  .contact-list li { display: flex; align-items: center; }
  .contact-icon { width: 10px; height: 10px; margin-right: 5px; fill: var(--brand-red); }
  .street-address {
    position: absolute;
    right: 25px;
    top: 202px;
    margin: 0;
    font-style: normal;
    text-align: right;
    font-size: 12px;
    line-height: 16px;
    color: var(--text-grey);
  }
  .footer-band { position: absolute; left: 0; bottom: 0; }
</style>
</head>
<body>
  <section class="card card--front" aria-label="Business card front">
    <svg class="name-tab" width="30" height="38" viewBox="0 0 30 38" aria-hidden="true">
      <polygon points="0,0 10,0 17,38 0,38" fill="var(--ink)"/>
      <polygon points="12,0 28,0 28,38 19,38" fill="var(--accent-red)"/>
    </svg>
    <h1 class="holder-name">DALE MORROW</h1>
    <p class="company-name">Qorvan Display Group Inc.</p>

    <ul class="contact-list">
      <li><svg class="contact-icon" viewBox="0 0 10 10"><path d="M1 4 Q5 0 9 4 L8 5 L6.5 4 L6.5 3 Q5 2.5 3.5 3 L3.5 4 L2 5 Z M2.5 6 L7.5 6 L8 9 L2 9 Z"/></svg>815-555-0142</li>
      <li><svg class="contact-icon" viewBox="0 0 10 10"><path d="M3 0 H7 Q8 0 8 1 V9 Q8 10 7 10 H3 Q2 10 2 9 V1 Q2 0 3 0 Z M3 1.5 V7.5 H7 V1.5 Z"/></svg>312-555-0187</li>
      <li><svg class="contact-icon" viewBox="0 0 10 10"><path d="M0 2 H10 V8 H0 Z" /><path d="M0 2 L5 6 L10 2" fill="none" stroke="#fff" stroke-width="1"/></svg>dmorrow@qorvanexhibits.net</li>
      <li><svg class="contact-icon" viewBox="0 0 10 10"><circle cx="5" cy="5" r="4.5"/><path d="M0.5 5 H9.5 M5 0.5 Q2.5 5 5 9.5 M5 0.5 Q7.5 5 5 9.5" fill="none" stroke="#fff" stroke-width="0.7"/></svg>www.qorvanexhibits.net</li>
    </ul>

    <address class="street-address">518 E Tollmere Ln<br>Arlington Heights,IL 60017</address>

    <svg class="footer-band" width="440" height="20" viewBox="0 0 440 20" aria-hidden="true">
      <polygon points="0,6 218,6 210,20 0,20" fill="var(--ink)"/>
      <polygon points="226,0 440,0 440,20 209,20" fill="var(--accent-red)"/>
    </svg>
  </section>

  <section class="card card--back" aria-label="Business card back">
    <p class="company-name">Qorvan Display Group Inc.</p>
  </section>
</body>
</html>
```